4D Cradle Glimpse Luxury Ultrasound Billboard

Design a HIGH-END, MODERN billboard for my private prenatal ultrasound studio, 4D Cradle Glimpse, located in Pace, Florida.
This billboard will be viewed by drivers traveling at highway speeds, so it must be extremely clean, simple, and readable within 6 seconds.
About My Business
4D Cradle Glimpse is a private prenatal ultrasound studio specializing in:
Highest technology 4D/HD Ultrasounds
Early Gender Determination
Pregnancy Confirmation
I have been serving families for nearly 10 years and is known for creating a memorable experience, not just an ultrasound appointment.
Design Style
I DO NOT want:
Flowers
Leaves
Swirls
Glitter
Hearts everywhere
Busy backgrounds
Generic maternity stock graphics
I DO want:
Modern
Luxury
Upscale
Clean
Professional
Eye-catching
Premium medical spa feel
Colors
Use colors from my logo:
LOGO Green ( or a deep green)
Black
White
Soft Gold accents
Images:
Incorporate my professional headshot in a clean, modern way, logo, and the ultrasound images
Text
Keep wording minimal.
Primary Headline ( OPEN TO IDEAS) :
EXAMPLES ( WOULD RATHER SOMETHING MORE CATCHY)
" ADVANCED IMAGING. UNFORGETTABLE MOMENTS"
"MEET YOUR BABY BEFORE BIRTH"
Under headline:
4D Ultrasound • Early Gender • Pregnancy Confirmation
Business Name:
4D Cradle Glimpse
Private Prenatal Ultrasound Studio
Phone Number:
850-471-5923
Important
This billboard must be readable in 5–6 seconds from a moving vehicle.
Less text is better.
The phone number and business name must be visible from a distance.
The design should feel like a premium brand that immediately tells expecting parents:
“This is where I go to see my baby.”
Files Provided
Official logo
Headshot
Ultrasound images
Don’t make this look like a medical office billboard.
Make it look like a luxury baby experience billboard. That’s what separates 4D Cradle Glimpse from hospitals, OB offices, and all the new studios popping up around you. The emotional connection is what gets moms to book. ❤️
Billboard Size - 10.6” x 36”

```html
<!DOCTYPE html>
<html lang="en">
<head>
<meta charset="utf-8">
<title>4D Cradle Glimpse – Billboard</title>
<link rel="stylesheet" href="https://fonts.googleapis.com/css2?family=Montserrat:wght@500;700;800;900&family=Kaushan+Script&family=Oswald:wght@600&family=Roboto+Condensed:wght@500&display=swap">
<style>
  :root {
    --green: #2c4a3c;
    --green-deep: #1f3a2e;
    --gold: #d4a03a;
    --gold-light: #f0c866;
    --white: #ffffff;
    --paper: #f1f1f1;
    --stage: #7a828b;
    --ink: #3a3a3a;
  }
  * { box-sizing: border-box; margin: 0; padding: 0; }
  html, body { width: 1145px; height: 1200px; overflow: hidden; }
  body { background: var(--stage); position: relative; font-family: "Montserrat", sans-serif; }

  .billboard {
    position: absolute; left: 37px; top: 439px; width: 1070px; height: 322px;
    background: linear-gradient(180deg, #fafafa 0%, var(--paper) 60%, #e6e6e6 100%);
    overflow: hidden; box-shadow: 0 8px 18px rgba(0,0,0,.35);
  }
  .headshot {
    position: absolute; left: 0; top: 0; width: 285px; height: 322px;
    background: radial-gradient(ellipse at 50% 35%, #e7c98d 0%, #c9a469 25%, #3d5b49 60%, #2f3f38 100%);
  }
  .band { position: absolute; inset: 0; width: 1070px; height: 322px; }

  .bracket { position: absolute; width: 60px; height: 34px; border: 0 solid var(--gold); }
  .bracket--tl { left: 234px; top: 16px; border-top-width: 3px; border-left-width: 3px; }
  .bracket--br { left: 777px; top: 88px; border-bottom-width: 3px; border-right-width: 3px; }

  .headline {
    position: absolute; left: 258px; top: 18px; width: 540px; text-align: center;
    font-weight: 900; font-size: 60px; line-height: 54px; color: var(--green-deep);
    letter-spacing: 1px; text-shadow: 0 3px 3px rgba(0,0,0,.25);
  }
  .headline .dot { color: var(--gold); }
  .tagline {
    position: absolute; left: 262px; top: 112px; width: 510px; text-align: center;
    font-family: "Kaushan Script", cursive; font-size: 40px; color: var(--gold);
    text-shadow: 0 2px 2px rgba(0,0,0,.2);
  }

  .services {
    position: absolute; left: 270px; top: 171px; width: 505px; height: 28px;
    background: var(--green); border-radius: 14px;
    display: flex; align-items: center; padding: 0 10px; gap: 7px;
    font-family: "Roboto Condensed", sans-serif; font-weight: 500; font-size: 15px; color: var(--white);
  }
  .service { display: flex; align-items: center; gap: 6px; }
  .service__icon { width: 22px; height: 22px; border-radius: 50%; background: var(--gold); flex: none; }
  .service__label--stacked { font-family: "Montserrat", sans-serif; font-size: 10.5px; line-height: 10px; font-weight: 500; }
  .sep { width: 5px; height: 5px; border-radius: 50%; background: var(--gold); }

  .brand {
    position: absolute; left: 284px; top: 207px; width: 305px; height: 96px;
    background: var(--white); border-radius: 10px; border: 2px solid #d9d9d9;
    box-shadow: 0 4px 8px rgba(0,0,0,.3);
    display: flex; flex-direction: column; align-items: center; justify-content: center; gap: 10px;
  }
  .brand__name { font-weight: 800; font-size: 27px; color: var(--gold); }
  .brand__sub {
    font-weight: 500; font-size: 9.5px; letter-spacing: 1px; color: var(--ink);
    display: flex; align-items: center; gap: 8px;
  }
  .brand__sub::before, .brand__sub::after { content: ""; width: 18px; height: 1px; background: var(--gold); }

  .phone { position: absolute; left: 612px; top: 242px; display: flex; align-items: center; gap: 12px; }
  .phone__icon {
    width: 62px; height: 62px; border-radius: 50%;
    background: radial-gradient(circle at 35% 30%, var(--gold-light), var(--gold) 70%);
    display: flex; align-items: center; justify-content: center;
  }
  .phone__number {
    font-family: "Oswald", sans-serif; font-weight: 600; font-size: 54px; color: var(--white);
    letter-spacing: 1px; text-shadow: 0 3px 4px rgba(0,0,0,.45);
  }

  .scan {
    position: absolute; left: 790px; top: 12px; width: 275px; height: 198px;
    border: 6px solid var(--white); transform: rotate(2deg);
    box-shadow: 0 4px 10px rgba(0,0,0,.35);
    background: radial-gradient(ellipse at 30% 45%, #c8643a 0%, #a44a26 40%, #2a130c 75%),
                #2a130c;
  }
</style>
</head>
<body>
  <section class="billboard">
    <div class="headshot" role="img" aria-label="Portrait of the studio owner in green scrubs holding an ultrasound probe"></div>

    <svg class="band" viewBox="0 0 1070 322" aria-hidden="true">
      <path d="M0,322 L0,306 C220,296 420,232 640,214 C820,200 950,198 1070,196 L1070,322 Z" fill="var(--green)"/>
      <path d="M600,218 C780,200 930,196 1070,192" fill="none" stroke="var(--gold)" stroke-width="5"/>
      <path d="M0,312 C160,306 300,286 420,258" fill="none" stroke="var(--gold)" stroke-width="6"/>
    </svg>

    <span class="bracket bracket--tl"></span>
    <span class="bracket bracket--br"></span>

    <h1 class="headline">ADVANCED<br>IMAGING<span class="dot">.</span></h1>
    <p class="tagline">Unforgettable Moments</p>

    <ul class="services">
      <li class="service"><span class="service__icon"></span><span>4D Ultrasound</span></li>
      <li class="sep"></li>
      <li class="service"><span class="service__icon"></span><span>Early Gender</span></li>
      <li class="sep"></li>
      <li class="service">
        <span class="service__icon"><svg width="22" height="22" viewBox="0 0 22 22"><circle cx="11" cy="11" r="7" fill="none" stroke="#fff" stroke-width="1.5"/><path d="M7.5 11 L10 13.5 L14.5 8.5" fill="none" stroke="#fff" stroke-width="2"/></svg></span>
        <span class="service__label--stacked">Pregnancy<br>Confirmation</span>
      </li>
    </ul>

    <div class="brand">
      <span class="brand__name">4D Cradle Glimpse</span>
      <span class="brand__sub">PRENATAL ULTRASOUND STUDIO</span>
    </div>

    <div class="phone">
      <span class="phone__icon">
        <svg width="32" height="32" viewBox="0 0 24 24"><path fill="#fff" d="M6.6 10.8c1.4 2.8 3.8 5.1 6.6 6.6l2.2-2.2c.3-.3.7-.4 1-.2 1.1.4 2.3.6 3.6.6.6 0 1 .4 1 1V20c0 .6-.4 1-1 1C10.6 21 3 13.4 3 4c0-.6.4-1 1-1h3.5c.6 0 1 .4 1 1 0 1.3.2 2.5.6 3.6.1.3 0 .7-.2 1L6.6 10.8z"/></svg>
      </span>
      <span class="phone__number">850-471-5923</span>
    </div>

    <div class="scan" role="img" aria-label="4D ultrasound image of twin babies side by side"></div>
  </section>
</body>
</html>
```